New Business Card Design Project

I need a design for business cards, i am an electrical business called "Corvane Electrical and Communications" i need the cards to be double sided with the company logo on the back (attached) the front needs to say my company name, web site, email address, telephone number, and ABN number and electrical license number. I am open to different arrangements of the information but would like the background to be incorporating something electrical or something that looks smart. open to all additional ideas also.

The company colours are orange and grey see logo attached.

Business Name: Corvane Electrical and Communications
Website: corvaneelectricalandcomms.example.com.au
Email: brent@corvaneelectricalandcomms.example.com.au
Telephone(mobile): 0481209736
ABN: 71208349162
Lic No: 418273D

Target Market(s)

Business entities, Project Managers, Accounts, Clients

Industry/Entity Type

Electrician

Contact Information for Business Card

I need a design for business cards, i am an electrical business called "Corvane Electrical and Communications" i need the cards to be double sided with the company logo on the back (attached) the front needs to say my company name

Font styles to use
Serif
Sans Serif

Colors
f37122
5c5c5c

Requirements
Must have
• Must have the Logo on the back open to different ways of it being on the back but had in mind to keep it central but again open to other options
Nice to have
• A real modern cool background that is eye catching yet contemporary
Should not have
• No backgrounds of a light bulb or plug or anything like that

```html
<!DOCTYPE html>
<html lang="en">
<head>
<meta charset="utf-8">
<title>Corvane Electrical and Communications – Business Cards</title>
<link rel="stylesheet" href="https://fonts.googleapis.com/css2?family=Source+Sans+3:wght@400;600&display=swap">
<style>
  :root {
    --backdrop: #3a3a3a;
    --card: #58585a;
    --accent: #f7a81b;
    --text: #ffffff;
    --text-soft: #ececec;
    --rule: #9a9a9c;
  }
  * { box-sizing: border-box; margin: 0; padding: 0; }
  html, body {
    width: 1105px;
    height: 1200px;
    overflow: hidden;
    background: var(--backdrop);
    font-family: "Source Sans 3", Arial, sans-serif;
    color: var(--text);
  }
  .card {
    position: absolute;
    left: 196px;
    width: 720px;
    height: 411px;
    background: var(--card);
    overflow: hidden;
  }
  .card--front { top: 146px; }
  .card--back { top: 602px; }

  .brand {
    position: absolute;
    right: 35px;
    top: 70px;
    width: 270px;
    text-align: right;
    font-weight: 600;
    color: var(--accent);
    line-height: 1.15;
  }
  .brand__name { display: block; font-size: 46px; letter-spacing: 2px; text-transform: uppercase; }
  .brand__line { display: block; font-size: 14px; letter-spacing: 0.6px; text-transform: uppercase; margin-top: 4px; }

  .holder {
    position: absolute;
    left: 35px;
    top: 212px;
  }
  .holder__name {
    font-size: 24px;
    font-weight: 600;
    color: var(--accent);
    letter-spacing: 0.5px;
    line-height: 1;
  }
  .holder__role {
    font-size: 18px;
    color: var(--text-soft);
    margin-top: 6px;
    line-height: 1;
  }
  .holder-rule {
    position: absolute;
    left: 179px;
    right: 35px;
    top: 257px;
    height: 1px;
    background: var(--rule);
  }

  .contacts {
    position: absolute;
    left: 36px;
    top: 284px;
    list-style: none;
  }
  .contacts__item {
    display: flex;
    align-items: center;
    height: 27.5px;
    font-size: 17.5px;
    color: var(--text-soft);
  }
  .contacts__icon { width: 16px; height: 16px; margin-right: 9px; flex: none; }

  .registration {
    position: absolute;
    right: 35px;
    top: 307px;
    text-align: right;
    font-size: 17.5px;
    line-height: 25px;
    color: var(--text-soft);
  }

  .stripe {
    position: absolute;
    left: 0;
    right: 0;
    bottom: 0;
    height: 12px;
  }

  .back-brand {
    position: absolute;
    left: 0;
    right: 0;
    top: 180px;
    text-align: center;
    font-size: 62px;
    font-weight: 600;
    letter-spacing: 4px;
    text-transform: uppercase;
    color: var(--accent);
    line-height: 1;
  }
  .back-url {
    position: absolute;
    left: 0;
    right: 0;
    top: 330px;
    text-align: center;
    font-size: 19px;
    letter-spacing: 1.2px;
    color: var(--text-soft);
  }
</style>
</head>
<body>

<section class="card card--front" aria-label="Business card front">
  <div class="brand">
    <span class="brand__name">Corvane</span>
    <span class="brand__line">Electrical &amp; Communications</span>
  </div>

  <div class="holder">
    <p class="holder__name">DALE HARWOOD</p>
    <p class="holder__role">CEO/FOUNDER</p>
  </div>
  <div class="holder-rule"></div>

  <ul class="contacts">
    <li class="contacts__item">
      <svg class="contacts__icon" viewBox="0 0 16 16" aria-hidden="true">
        <rect x="3.5" y="0.5" width="9" height="15" rx="1.5" fill="none" stroke="#f7a81b" stroke-width="1.6"/>
        <rect x="6" y="12" width="4" height="1.5" fill="#f7a81b"/>
      </svg>
      0481209736
    </li>
    <li class="contacts__item">
      <svg class="contacts__icon" viewBox="0 0 16 16" aria-hidden="true">
        <rect x="1" y="3.5" width="14" height="9.5" fill="#f7a81b"/>
        <path d="M1 3.5 L8 9 L15 3.5" fill="none" stroke="#58585a" stroke-width="1.3"/>
      </svg>
      brent@corvaneelectricalandcomms.example.com.au
    </li>
    <li class="contacts__item">
      <svg class="contacts__icon" viewBox="0 0 16 16" aria-hidden="true">
        <circle cx="8" cy="8" r="7" fill="#f7a81b"/>
        <path d="M8 1 C5 4 5 12 8 15 M8 1 C11 4 11 12 8 15 M1 8 H15" fill="none" stroke="#58585a" stroke-width="1"/>
      </svg>
      corvaneelectricalandcomms.example.com.au
    </li>
  </ul>

  <div class="registration">
    <p>ABN: 71208349162</p>
    <p>Lic No: 418273D</p>
  </div>

  <svg class="stripe" viewBox="0 0 720 12" preserveAspectRatio="none" aria-hidden="true">
    <polygon points="0,0 474,0 470,12 0,12" fill="#f7a81b"/>
    <polygon points="481,0 720,0 720,12 477,12" fill="#ffffff"/>
  </svg>
</section>

<section class="card card--back" aria-label="Business card back">
  <p class="back-brand">Corvane</p>
  <p class="back-url">www.corvaneelectricalandcomms.example.com.au</p>
</section>

</body>
</html>
```